Website for a Psychologist in Private Practice

I need a cool web design for my website: www.drkalvoric.com. I would like it to look professional. Keep all the current content and add: Space for video; radio spots (see Silver Cedar Tunes Logo below for those); Quick Inquiry; Friendora link; 5 star rating on Rivo; a map; reviews from former patients. I am open to suggestions.

Target Market(s)

Those seeking individual and marital counseling.

Industry/Entity Type

Mental Health

Number of Pages Required

1 page

Font styles to use
Sans Serif
Other font styles liked:
• I'm open but no hard to read script

Requirements
Must have
• All the content on my home page with link for video and radio spots. List services and degrees and expertices (pics not necessary).
Nice to have
• A video of me and radio conversations (logo of Silver Cedar Tunes radio attached).
Should not have
• Cartoons, comedy, etc.... I don't need pictures of services (marital, depression, etc...) Just list those.

```html
<!DOCTYPE html>
<html lang="en">
<head>
<meta charset="utf-8">
<title>Dr. Marla J. Kalvoric – Clinical Psychologist</title>
<link rel="stylesheet" href="https://fonts.googleapis.com/css2?family=Roboto:wght@400;500;700&family=Josefin+Sans:wght@300;400;600;700&display=swap">
<style>
:root{
  --gold:#c7a84c;
  --gold-dark:#b18f35;
  --sand:#d9ccb9;
  --sand-light:#e3d8c8;
  --ink:#3d3a35;
  --muted:#6c665d;
  --navy:#1f5a84;
  --navy-dark:#184a6e;
  --sky:#3b8fc9;
  --white:#ffffff;
  --line:#8c8478;
}
*{box-sizing:border-box;margin:0;padding:0}
html,body{width:1200px;height:3163px;overflow:hidden}
body{position:relative;background:var(--sand);font-family:'Roboto',sans-serif;color:var(--ink)}
.abs{position:absolute}

/* top contact strip */
.topbar{left:0;top:0;width:1200px;height:52px;background:var(--white);display:flex;align-items:center;padding-left:72px;gap:42px;font-size:14px;color:var(--muted)}
.topbar span{display:flex;align-items:center;gap:9px}

/* header */
.site-header{left:0;top:52px;width:1200px;height:44px;background:var(--gold);display:flex;align-items:center;justify-content:space-between;padding:0 72px}
.brand{font-family:'Josefin Sans',sans-serif;font-size:32px;color:var(--white);font-weight:300;padding-top:6px}
.brand b{font-weight:400}
.nav{display:flex;gap:20px;font-size:15px;font-weight:700;color:var(--white)}

/* hero */
.hero-bg{left:0;top:96px;width:1200px;height:1060px;background:linear-gradient(180deg,#6fb7cf 0%,#8ec7d6 35%,#a7cfd3 60%,#cfd8cf 80%,var(--sand) 100%)}
.slider{left:93px;top:179px;width:1012px;height:492px;background:rgba(255,255,255,.55);padding:14px}
.slide{width:100%;height:100%;background:linear-gradient(90deg,#2e3b22 0%,#8a7a3a 30%,#d8b86a 42%,#4b6a3a 55%,#c9b39c 70%,#5b87ad 100%);position:relative}
.slide-title{position:absolute;left:60px;top:196px;font-size:32px;line-height:36px;color:var(--white);font-weight:500;text-shadow:0 1px 3px rgba(0,0,0,.5)}
.slide-caption{position:absolute;right:210px;bottom:16px;font-size:17px;color:var(--white);font-weight:700}
.slide-arrow{position:absolute;top:228px;width:32px;height:32px;border-radius:50%;border:2px solid rgba(255,255,255,.8);background:rgba(0,0,0,.25)}

.video-label{left:95px;top:890px;font-family:'Josefin Sans',sans-serif;font-size:21px;font-weight:600;color:#1a1a1a}
.video{left:295px;top:742px;width:612px;height:351px;background:var(--white);padding:9px}
.video-screen{width:100%;height:100%;background:linear-gradient(180deg,#0b2b3a 0%,#1f6c7e 40%,#3bb1b5 65%,#0f3b44 100%);position:relative}
.video-bar{position:absolute;left:0;bottom:0;width:100%;height:26px;background:rgba(0,0,0,.55)}
.video-progress{position:absolute;left:10px;bottom:22px;width:574px;height:3px;background:rgba(255,255,255,.35)}
.video-progress i{display:block;width:150px;height:3px;background:#e52d27}

/* radio + expertise */
.rule{left:249px;width:711px;height:14px}
.radio-img{left:95px;top:1213px;width:137px;height:127px;border-radius:14px;background:linear-gradient(180deg,#8a5a35,#5a3a22)}
.radio-title{left:264px;top:1222px;font-family:'Josefin Sans',sans-serif;font-size:38px;font-weight:700;color:#4a3422}
.radio-show{left:268px;top:1276px;width:297px;height:46px;display:flex;align-items:center;gap:10px;font-family:'Josefin Sans',sans-serif;font-size:24px;font-weight:600;color:#c51f66}
.radio-show i{width:14px;height:14px;background:#c51f66;display:block}
.divider-v{left:601px;top:1184px;width:1px;height:176px;background:#b6aa98}
.expertise{left:601px;top:1218px;width:536px;text-align:center;font-family:'Josefin Sans',sans-serif;color:var(--muted)}
.expertise h3{font-size:24px;font-weight:400;color:#5a4a3a;letter-spacing:1px}
.expertise h3 span{color:#b4612f;letter-spacing:-2px}
.expertise p{font-size:15px;margin-top:6px;word-spacing:14px}
.expertise .sub{font-size:20px;margin-top:4px;word-spacing:0}

/* welcome */
.welcome{left:76px;top:1425px;width:685px}
.welcome h1{font-family:'Josefin Sans',sans-serif;font-weight:300;font-size:30px;line-height:30px;color:#2b2824}
.welcome h1 b{font-weight:600;font-size:34px}
.welcome p{font-size:13.6px;line-height:25px;color:#4a453e;margin-top:16px}
.welcome p:first-of-type{margin-top:12px}

.inquiry{left:795px;top:1430px;width:327px;height:500px;background:var(--white);border-radius:6px;box-shadow:0 0 10px rgba(0,0,0,.2);overflow:hidden}
.inquiry-head{background:var(--gold);height:126px;text-align:center;color:var(--white);padding-top:12px;clip-path:polygon(0 0,100% 0,100% 86%,50% 100%,0 86%)}
.inquiry-head .kicker{font-size:16px;font-weight:500}
.inquiry-head .pill{margin:6px auto 0;width:290px;height:36px;background:var(--sky);border-radius:18px;font-size:29px;line-height:38px;letter-spacing:1px}
.inquiry-head .note{font-size:12.5px;margin-top:6px;line-height:16px}
.inquiry form{padding:22px 17px 0}
.field{width:100%;height:38px;background:#eeeeee;border-radius:3px;margin-bottom:11px;font-size:13px;color:#555;padding:10px 12px}
.field.area{height:105px}
.submit{width:100%;height:40px;background:#7fa6d3;border-radius:3px;color:var(--white);text-align:center;font-weight:700;font-size:15px;line-height:40px;margin-top:4px}

/* reviews */
.reviews-title{left:0;top:2020px;width:1200px;text-align:center;font-family:'Josefin Sans',sans-serif;font-size:29px;color:#2b2824}
.review{top:2118px;width:330px;text-align:center}
.avatar{width:76px;height:76px;border-radius:50%;margin:0 auto;background:linear-gradient(180deg,#c9b6a0,#7a6454);border:3px solid var(--white)}
.review p{font-size:13.4px;line-height:20.5px;margin-top:30px;color:#2b2824}
.review .name{font-family:'Josefin Sans',sans-serif;font-size:18px;margin-top:28px}
.review .role{font-size:12px;margin-top:2px}
.review-rule{top:2210px;width:1px;height:200px;background:#c2b6a4}

.donate{left:0;top:2535px;width:1200px;text-align:center;font-family:'Josefin Sans',sans-serif;font-size:22px;color:#2b2824}
.partner{top:2577px;width:242px;height:106px;background:var(--white)}
.partner i{position:absolute;left:50%;top:50%;transform:translate(-50%,-50%);width:150px;height:54px;background:#e7dfd2;border-radius:6px}

/* footer */
.footer-wave{left:0;top:2720px;width:1200px;height:90px}
.footer{left:0;top:2800px;width:1200px;height:305px;background:var(--navy);color:var(--white)}
.fcol{top:74px;font-size:13px;line-height:24px}
.fcol h4{font-size:13.5px;font-weight:700;text-transform:uppercase;line-height:18px}
.fcol .lic{line-height:18px;margin-bottom:10px}
.contact-row{display:flex;gap:12px;align-items:flex-start;margin-bottom:14px;line-height:20px}
.contact-row.big{font-size:19px}
.map{left:614px;top:118px;width:240px;height:162px;background:linear-gradient(135deg,#e8e4dc,#d5d0c6)}
.bottombar{left:0;top:3105px;width:1200px;height:58px;background:var(--gold);display:flex;align-items:center;justify-content:space-between;padding:0 74px 0 76px;color:var(--white);font-size:13px}
.social{display:flex;gap:26px}
.social span{display:flex;align-items:center;gap:8px}
.social i{width:12px;height:12px;border-radius:50%;background:var(--white);display:block}
</style>
</head>
<body>

<div class="abs topbar">
  <span><svg width="12" height="16" viewBox="0 0 12 16"><path d="M6 0a6 6 0 0 0-6 6c0 4.5 6 10 6 10s6-5.5 6-10a6 6 0 0 0-6-6zm0 8.5A2.5 2.5 0 1 1 6 3.5a2.5 2.5 0 0 1 0 5z" fill="#3b8fc9"/></svg>418 Heron Lane #120, Bayview Harbor, CA. 90417</span>
  <span><svg width="16" height="16" viewBox="0 0 16 16"><path d="M3.5 1l3 3-2 2c1 2 3 4 5 5l2-2 3 3-2 3C6 14 2 10 1 3.5z" fill="none" stroke="#888" stroke-width="1.3"/></svg>Call Now: (555) 318 2047</span>
  <span><svg width="16" height="12" viewBox="0 0 16 12"><rect x=".7" y=".7" width="14.6" height="10.6" fill="none" stroke="#3b8fc9" stroke-width="1.3"/><path d="M1 1l7 6 7-6" fill="none" stroke="#3b8fc9" stroke-width="1.3"/></svg>Email: mk@drkalvoric.com</span>
</div>

<header class="abs site-header">
  <div class="brand">Dr. <b>Marla J. Kalvoric</b></div>
  <nav class="nav"><span>HOME</span><span>SESSIONS</span><span>RESOURCES</span><span>BIO</span><span>CONTACT</span></nav>
</header>

<div class="abs hero-bg" role="img" aria-label="Background of turquoise sea water meeting a sandy beach"></div>

<section class="abs slider">
  <div class="slide" role="img" aria-label="Sunlit forest scene beside a portrait of the psychologist">
    <div class="slide-title">Lorem ipsum dolor sit<br>amet, consectetur<br>adipiscing elit</div>
    <div class="slide-caption">Dr. Marla K</div>
    <div class="slide-arrow" style="left:4px"></div>
    <div class="slide-arrow" style="right:4px"></div>
  </div>
</section>

<div class="abs video-label">Watch Our Video</div>
<section class="abs video">
  <div class="video-screen" role="img" aria-label="Video still of a calm lake at dusk with rocks">
    <div class="video-progress"><i></i></div>
    <div class="video-bar"></div>
  </div>
</section>

<svg class="abs rule" style="top:1166px" viewBox="0 0 711 14"><path d="M8 7H703" stroke="#8c8478" stroke-width="2"/><path d="M0 7l10-6v12zM711 7l-10-6v12z" fill="#8c8478"/></svg>
<svg class="abs rule" style="top:1364px" viewBox="0 0 711 14"><path d="M8 7H703" stroke="#8c8478" stroke-width="2"/><path d="M0 7l10-6v12zM711 7l-10-6v12z" fill="#8c8478"/></svg>

<div class="abs radio-img" role="img" aria-label="Vintage wooden radio"></div>
<div class="abs radio-title">Radio Spots</div>
<div class="abs radio-show"><i></i>Silver Cedar Tunes</div>
<div class="abs divider-v"></div>
<div class="abs expertise">
  <h3><span>~~~~</span> EXPERTISE <span>~~~~</span></h3>
  <p>Dating Marriage Parenting&nbsp;&amp;&nbsp;Professional</p>
  <p class="sub">RELATIONSHIPS</p>
  <p>Depression&nbsp;&amp;&nbsp;Anxiety&nbsp;Issues Personality&nbsp;Disorders Life&nbsp;Management</p>
</div>

<section class="abs welcome">
  <h1>Welcome to<br><b>Dr. Marla J. Kalvoric</b></h1>
  <p>I'm so glad you are here. Choosing to see a professional for issues in your life can be difficult but also possibly life changing. Many postpone seeking help because they believe doing so acknowledges failure on their part. Really? We seek the help of experts all the time (contractors, mechanics, chefs, etc...) and what is more important than your life? Consulting with a neutral party to act in your best interest can be time well spent. So if you are willing to take the time to invest in counseling, make sure that it is with someone that is worth your time.</p>
  <p>Choose a licensed psychologist with a doctoral degree (Ph.D. or PsyD.) - both have over 10 years of education in the field of psychology, extensive internships and comprehensive licensing exams. Others have far less education if any. Also, consider the therapist's approach to therapy. I use a straightforward approach (psychobabble available upon request) with brief, solution-oriented sessions.</p>
  <p>Experience also separates good psychologists from others with fewer and more proficient sessions. My 20+ years of professional experience and my life experience contributes to the empathetic perspective I use to relate to each person I see. I also believe it is the reason 90% of my practice is referral based and why many other psychologists in the area seek my services.</p>
  <p><b>DO NOT COMPROMISE.</b> Find an educated, licensed, experienced professional that you can relate to. Think about what it took to get you here and the importance resolving this issue can have on your life.</p>
</section>

<aside class="abs inquiry">
  <div class="inquiry-head">
    <div class="kicker">CONTACT US TODAY FOR YOUR</div>
    <div class="pill">QUICK INQUIRY</div>
    <div class="note">Fill out the form below and we'll be in touch<br>within 24 hours!</div>
  </div>
  <form>
    <div class="field">Name</div>
    <div class="field">Email</div>
    <div class="field">Phone</div>
    <div class="field area">How Can we help you?</div>
    <div class="submit">SUBMIT</div>
  </form>
</aside>

<h2 class="abs reviews-title">Reviews From Patients</h2>
<div class="abs review-rule" style="left:420px"></div>
<div class="abs review-rule" style="left:782px"></div>
<article class="abs review" style="left:73px">
  <div class="avatar" role="img" aria-label="Patient portrait"></div>
  <p>Lorem ipsum dolor sit amet, consectetur adipiscing elit, sed do eiusmod tempor incididunt ut labore et dolore magna aliqua. Ut enim ad minim veniam, quis nostrud exercitation ullamco laboris nisi ut aliquip ex ea commodo consequat. Duis aute irure dolor in reprehenderit in voluptate velit esse cillum dolore eu fugiat nulla pariatur. Excepteur sint occaecat cupidatat non proident, sunt in culpa qui officia deserunt mollit anim id est laborum.</p>
  <div class="name">Sam Ortega</div><div class="role">Lorem ipsum dolor</div>
</article>
<article class="abs review" style="left:436px">
  <div class="avatar" role="img" aria-label="Patient portrait"></div>
  <p>Lorem ipsum dolor sit amet, consectetur adipiscing elit, sed do eiusmod tempor incididunt ut labore et dolore magna aliqua. Ut enim ad minim veniam, quis nostrud exercitation ullamco laboris nisi ut aliquip ex ea commodo consequat. Duis aute irure dolor in reprehenderit in voluptate velit esse cillum dolore eu fugiat nulla pariatur. Excepteur sint occaecat cupidatat non proident, sunt in culpa qui officia deserunt mollit anim id est laborum.</p>
  <div class="name">Sam Ortega</div><div class="role">Lorem ipsum dolor</div>
</article>
<article class="abs review" style="left:799px">
  <div class="avatar" role="img" aria-label="Patient portrait"></div>
  <p>Lorem ipsum dolor sit amet, consectetur adipiscing elit, sed do eiusmod tempor incididunt ut labore et dolore magna aliqua. Ut enim ad minim veniam, quis nostrud exercitation ullamco laboris nisi ut aliquip ex ea commodo consequat. Duis aute irure dolor in reprehenderit in voluptate velit esse cillum dolore eu fugiat nulla pariatur. Excepteur sint occaecat cupidatat non proident, sunt in culpa qui officia deserunt mollit anim id est laborum.</p>
  <div class="name">Sam Ortega</div><div class="role">Lorem ipsum dolor</div>
</article>

<div class="abs donate">A portion of all revenue is donated to</div>
<div class="abs partner" style="left:352px" role="img" aria-label="Partner charity badge"><i></i></div>
<div class="abs partner" style="left:605px" role="img" aria-label="Partner charity badge"><i></i></div>

<svg class="abs footer-wave" viewBox="0 0 1200 90" preserveAspectRatio="none">
  <path d="M0 70 C300 0 800 0 1200 30 V90 H0Z" fill="#ffffff"/>
  <path d="M0 84 C300 14 800 14 1200 44 V90 H0Z" fill="#1f5a84"/>
</svg>

<footer class="abs footer">
  <div class="abs fcol" style="left:74px;width:250px">
    <h4>Clinical Psychologist</h4>
    <div class="lic">California # PSY20581</div>
    <div>Doctoral Degree in Clinical Psychology</div>
    <div>Masters Degree in Counseling</div>
    <div>Psychology Doctoral Internship, Coastal U.</div>
    <div>Medical Center Masters Internship,</div>
    <div>Westbrook Clinic</div>
  </div>
  <div class="abs fcol" style="left:344px;width:250px">
    <h4 style="margin-bottom:24px">Contact Information</h4>
    <div class="contact-row"><svg width="16" height="20" viewBox="0 0 12 16"><path d="M6 0a6 6 0 0 0-6 6c0 4.5 6 10 6 10s6-5.5 6-10a6 6 0 0 0-6-6zm0 8.5A2.5 2.5 0 1 1 6 3.5a2.5 2.5 0 0 1 0 5z" fill="#fff"/></svg><span>418 Heron Lane, Suite 120<br>Bayview Harbor, CA 90417</span></div>
    <div class="contact-row big"><svg width="18" height="18" viewBox="0 0 16 16"><path d="M3.5 1l3 3-2 2c1 2 3 4 5 5l2-2 3 3-2 3C6 14 2 10 1 3.5z" fill="#fff"/></svg><span>(555) 318 2047</span></div>
    <div class="contact-row" style="margin-top:18px"><svg width="20" height="15" viewBox="0 0 16 12"><rect width="16" height="12" fill="#fff"/><path d="M1 1l7 6 7-6" fill="none" stroke="#1f5a84" stroke-width="1.3"/></svg><span>mk@drkalvoric.com</span></div>
  </div>
  <div class="abs fcol" style="left:614px"><h4>Find us on map</h4></div>
  <div class="abs map" role="img" aria-label="Street map showing the office location"></div>
  <div class="abs fcol" style="left:884px">
    <h4 style="margin-bottom:22px">Quick Links</h4>
    <div>Home</div><div>Sessions</div><div>Resources</div><div>Bio</div><div>Contact</div>
  </div>
</footer>

<div class="abs bottombar">
  <span>©2016 Dr. Marla J. Kalvoric. All Rights Reserved.</span>
  <div class="social"><span><i></i>Rivo</span><span><i></i>Friendora</span><span><i></i>Chirpline</span></div>
</div>

</body>
</html>
```